Migration and redesign of existing website to WordPress using DIVI 3

I. TASK OBJECTIVE:
- Redesign our existing website www.kelvaleheelcare.com.au with a fresh new look and migrate to new Wordpress site based on DIVI3 theme. The site will contain the same basic functionality as the existing site (with some small changes).

II. STYLE/ DESIGN ASPECT:
As an example of a site that I like the look of, see https://pebblequarn.com/. I like the use of shadows, and this would go well with the little animations you can do with Divi (e.g. when hovering over pics).

1. What I am looking for is a design which has lots of white space, is modern and friendly looking (but still not too cute or frivolous, as we are a medical practice)
2. DESIGN that is NOT TOO rectangular or blocky.
3. Please take into consideration our Users are Older market, so any icons or navigation features need to be very easy to understand and not too small.
4. Must be easy to navigate
5. We are are happy to go with a new colour scheme, and are working on some ideas for this, but happy to take suggestions.

III. SPECIFICATIONS:
1. 5+ Pages (should flow like the current site)
2. Using Wordpress Divi 3 theme.
3. I'd like every page to have a "book now" button and a contact form in a sidebar so that users can click the button or fill in the contact form without scrolling at all. EXCEPT ON THE HOME PAGE, where there should still be a book now button (maybe on the top right in the header of all pages?), and maybe a contact us button which scrolls down to the contact area at the bottom of the HOME page. I don't think a side bar is necessarily required on the home page, but if you think it makes sense from a design perspective please let me know.
4. AT THE BOTTOM OF THE PAGE, just above the FOOTER, I'd like a row of trust logos for various organisations that we are affiliated with. (A list of this company will be provided later but you could temporarily use placeholders)

Once we have a structure in place, we can migrate most of the content. Please let me know if I'm not being clear or you need further information.

Podiatry Customers and Referrors

Health Care

5+ page

• Simple to navigate.
• Contact/booking details on most if not all pages - please see specification above
• Section for Trusted Affiliates above the footer
• Wordpress using Divi3 Theme
• Not too busy with the design. Plenty of white space or light background.
• Should not be complicated to navigate.
• TOO rectangular or blocky designs

```html
<!DOCTYPE html>
<html lang="en">
<head>
<meta charset="utf-8">
<title>Kelvale Heel Care – Podiatry</title>
<link href="https://fonts.googleapis.com/css2?family=Open+Sans:wght@400;600;700&family=Raleway:wght@400;500;600;700&display=swap" rel="stylesheet">
<style>
:root{
  --blue:#1c9bd3;
  --blue-dark:#0f7cb0;
  --blue-deep:#0b5f8c;
  --blue-pale:#e6f4fb;
  --ink:#333a40;
  --muted:#6d757c;
  --line:#e3e7ea;
  --grey-bg:#f4f6f7;
  --white:#ffffff;
}
*{box-sizing:border-box;margin:0;padding:0}
html,body{width:1200px;height:3592px;overflow:hidden}
body{font-family:"Open Sans",Arial,sans-serif;color:var(--ink);background:var(--white);position:relative;font-size:14px;line-height:1.55}
h1,h2,h3,h4{font-family:"Raleway",Arial,sans-serif;font-weight:500}
.abs{position:absolute}
.btn{display:inline-flex;align-items:center;gap:8px;background:var(--blue);color:var(--white);font-size:12px;font-weight:700;letter-spacing:1px;padding:9px 18px;text-transform:uppercase;border-radius:2px}
.btn-outline{background:transparent;border:2px solid var(--white);font-size:15px;padding:10px 26px}
.square{display:inline-block;width:30px;height:30px;background:var(--blue);border-radius:2px}
.placeholder{display:block}

/* header */
.site-header{left:0;top:0;width:1200px;height:140px;background:var(--white);box-shadow:0 2px 10px rgba(0,0,0,.08)}
.brand{left:100px;top:40px;display:flex;align-items:center;gap:14px}
.brand-dot{width:56px;height:56px;border-radius:50%;background:var(--blue-pale);border:3px solid var(--blue)}
.brand-name{font-family:"Raleway",sans-serif;font-weight:600;font-size:22px;color:var(--blue-dark)}
.header-right{right:100px;top:52px;display:flex;align-items:center;gap:10px}
.call{display:flex;align-items:center;gap:10px;font-weight:700;color:var(--blue-dark);font-size:17px;margin-right:20px}
.menu-toggle{margin-left:18px;width:34px}
.menu-toggle span{display:block;height:4px;background:var(--blue);margin:5px 0;border-radius:2px}

/* hero */
.hero{left:0;top:140px;width:1200px;height:360px;background:linear-gradient(160deg,#5f7f92 0%,#8aa6b6 35%,#3d5b6e 70%,#24394a 100%)}
.hero-text{left:0;top:100px;width:1200px;text-align:center;color:var(--white)}
.hero-text h1{font-size:40px;font-weight:400;line-height:1.2;text-shadow:0 2px 8px rgba(0,0,0,.35)}
.hero-text .btn{margin-top:22px}
.slide-arrow{top:160px;width:40px;height:40px;background:rgba(28,155,211,.85);display:flex;align-items:center;justify-content:center}

/* practice */
.section-icon{left:560px;top:540px;width:80px;height:80px;border-radius:50%;background:var(--blue);border:6px solid var(--blue-pale);display:flex;align-items:center;justify-content:center}
.section-title{width:1200px;left:0;text-align:center;font-size:38px;color:var(--blue-dark)}
.cards{left:100px;top:700px;display:flex;gap:8px}
.card{width:244px;height:560px;background:var(--white);box-shadow:0 4px 16px rgba(0,0,0,.12);position:relative;text-align:center}
.card .placeholder{height:280px}
.card h3{font-size:20px;margin:26px 0 14px;color:var(--ink)}
.card p{font-size:12px;color:var(--muted);padding:0 18px;line-height:1.6}
.card .btn{position:absolute;left:50%;transform:translateX(-50%);bottom:22px;white-space:nowrap}
.card.is-featured{background:var(--blue)}
.card.is-featured h3,.card.is-featured p{color:var(--white)}
.card.is-featured .btn{background:var(--white);color:var(--blue)}

/* features */
.features-photo{left:100px;top:1330px;width:460px;height:440px}
.features h2{left:620px;top:1350px;width:480px;text-align:center;font-size:38px;color:var(--blue-dark)}
.feature-bar{left:620px;width:480px;height:62px;background:var(--blue);color:var(--white);font-size:14px;font-weight:600;padding:10px 20px 10px 26px;line-height:1.45}
.feature-bar::after{content:"";position:absolute;right:0;top:0;border-style:solid;border-width:0 24px 24px 0;border-color:transparent var(--blue-dark) transparent transparent}
.feature-copy{left:620px;top:1510px;width:480px;font-size:13px;color:var(--muted);padding-left:26px}

/* team */
.team-title{top:1830px}
.team-arrows{right:100px;top:1842px;display:flex;gap:4px}
.team-arrows span{width:32px;height:32px;background:var(--blue);display:flex;align-items:center;justify-content:center}
.team-arrows span.is-light{background:var(--blue-pale)}
.team-row{left:100px;top:1910px;display:flex;gap:8px}
.member{width:194px;height:310px;position:relative}
.member-edge{width:28px;height:310px;background:var(--blue)}
.member.is-active{box-shadow:0 6px 18px rgba(0,0,0,.2)}
.member-caption{position:absolute;left:0;bottom:0;width:100%;background:rgba(15,124,176,.92);color:var(--white);padding:12px 14px;font-size:12px}
.member-caption strong{display:block;font-size:14px}

/* cases and book */
.band{left:0;top:2270px;width:1200px;height:620px;background:linear-gradient(180deg,#4fb5e2 0%,var(--blue) 55%,#49b0de 100%)}
.band-title{color:var(--white);font-size:36px}
.case{left:100px;width:500px;height:200px;display:flex;background:var(--white);box-shadow:0 4px 14px rgba(0,0,0,.15)}
.case .placeholder{width:190px;height:200px}
.case-body{padding:20px 22px}
.case-body h3{font-size:22px;color:var(--blue-dark);font-weight:600}
.case-body .tag{font-size:11px;color:var(--muted);text-transform:uppercase;letter-spacing:1px}
.case-body p{font-size:12px;color:var(--muted);margin:10px 0 14px;line-height:1.5}
.case-body .icons{display:flex;gap:6px}
.case-body .icons .square{width:28px;height:28px}
.book-title{left:660px;top:2370px;width:260px;color:var(--white);font-family:"Raleway",sans-serif;font-size:30px;font-weight:700;line-height:1.2}
.book-cover{left:930px;top:2360px;width:180px;height:240px;background:var(--white);padding:10px;box-shadow:0 6px 18px rgba(0,0,0,.2)}
.book-cover .cover-head{background:var(--blue-deep);color:var(--white);font-family:"Raleway",sans-serif;font-weight:700;font-size:16px;padding:10px;height:80px;line-height:1.2}
.book-cover .cover-head small{display:block;font-size:9px;font-weight:400;margin-top:6px}
.book-cover .placeholder{height:140px}
.book-copy{left:660px;top:2650px;width:440px;color:var(--white);font-size:13px}
.book-btn{left:820px;top:2770px}

/* contact */
.contact-title{top:2930px}
.contact-sub{left:0;top:2985px;width:1200px;text-align:center;color:var(--blue);font-size:14px}
.contact-info{left:140px;top:3060px;width:220px}
.contact-info h4{font-size:20px;color:var(--blue-dark);font-weight:600;margin-bottom:8px}
.contact-info p{font-size:13px;color:var(--muted);margin-bottom:30px;display:flex;gap:8px;align-items:center}
.map{left:370px;top:3060px;width:300px;height:300px}
.form{left:720px;top:3060px;width:340px}
.field{border:1px solid var(--line);height:36px;margin-bottom:12px;padding:8px 12px;font-size:12px;color:var(--muted)}
.field.is-area{height:100px}

/* footer */
.footer-nav{left:0;top:3470px;width:1200px;height:60px;background:var(--grey-bg);border-top:1px solid var(--line);display:flex;justify-content:center;align-items:center;gap:40px;font-size:13px;color:var(--ink)}
.footer-bottom{left:0;top:3530px;width:1200px;height:62px;background:var(--white);border-top:1px solid var(--line)}
.copyright{left:100px;top:22px;font-size:11px;color:var(--muted)}
.footer-social{right:140px;top:16px;display:flex;gap:6px}
</style>
</head>
<body>

<header class="site-header abs">
  <div class="brand abs"><span class="brand-dot"></span><span class="brand-name">Kelvale Heel Care</span></div>
  <div class="header-right abs">
    <div class="call">
      <span class="square" style="display:flex;align-items:center;justify-content:center">
        <svg width="16" height="16" viewBox="0 0 24 24"><path fill="#fff" d="M6.6 10.8a15 15 0 006.6 6.6l2.2-2.2c.3-.3.7-.4 1-.2 1.1.4 2.3.6 3.6.6.6 0 1 .4 1 1V20c0 .6-.4 1-1 1A17 17 0 013 4c0-.6.4-1 1-1h3.5c.6 0 1 .4 1 1 0 1.3.2 2.5.6 3.6.1.3 0 .7-.2 1z"/></svg>
      </span>
      Call: (08) 5550 1820
    </div>
    <span class="square"></span><span class="square"></span><span class="square"></span><span class="square"></span><span class="square"></span>
    <div class="menu-toggle"><span></span><span></span><span></span></div>
  </div>
</header>

<section class="hero abs" role="img" aria-label="Photo of feet stepping through splashing water">
  <div class="slide-arrow abs" style="left:20px"><svg width="14" height="14" viewBox="0 0 14 14"><path d="M9 2L4 7l5 5" stroke="#fff" stroke-width="2" fill="none"/></svg></div>
  <div class="slide-arrow abs" style="right:20px"><svg width="14" height="14" viewBox="0 0 14 14"><path d="M5 2l5 5-5 5" stroke="#fff" stroke-width="2" fill="none"/></svg></div>
  <div class="hero-text abs">
    <h1>We offer solutions<br>to common foot problems</h1>
    <span class="btn btn-outline">
      <svg width="16" height="16" viewBox="0 0 16 16"><rect x="2" y="3" width="12" height="11" fill="none" stroke="#fff" stroke-width="1.6"/><path d="M2 6h12M5 1v3M11 1v3" stroke="#fff" stroke-width="1.6"/></svg>
      Book Now
    </span>
  </div>
</section>

<div class="section-icon abs">
  <svg width="36" height="36" viewBox="0 0 36 36"><path d="M12 4c0 8-2 14-2 20 0 5 3 8 8 8h8c3 0 4-3 2-5-3-2-8-3-10-6-2-3-1-10-1-17z" fill="none" stroke="#fff" stroke-width="2.2" stroke-linejoin="round"/></svg>
</div>
<h2 class="section-title abs" style="top:630px">Practice Areas</h2>

<div class="cards abs">
  <article class="card">
    <span class="placeholder" role="img" aria-label="Photo of a podiatrist examining a patient's foot" style="background:linear-gradient(135deg,#e9ddd2,#c9b7a7)"></span>
    <h3>Common Problems</h3>
    <p>When you suffer from a foot or ankle problem, the pain and discomfort can make it a challenge to engage in simple daily activities. When the pain disrupts your life, you need to contact a skilled, experienced podiatrist to get treatment.</p>
    <span class="btn">View More</span>
  </article>
  <article class="card is-featured">
    <span class="placeholder" role="img" aria-label="Photo of a surgeon reviewing a foot x-ray" style="background:linear-gradient(135deg,#cfe2ee,#7fa8c2)"></span>
    <h3>Foot and Ankle Surgery</h3>
    <p>Foot and ankle pain can be extremely distracting and uncomfortable, and some conditions may require surgery. If you have a stubborn problem, our surgeon can assess your options and explain every step with care.</p>
    <span class="btn">View More</span>
  </article>
  <article class="card">
    <span class="placeholder" role="img" aria-label="Photo of a smiling runner tying a sports shoe" style="background:linear-gradient(135deg,#f0e2d6,#d3b59c)"></span>
    <h3>Sports &amp; Dance</h3>
    <p>Sports podiatry groups injuries and concerns seen in those that train and compete regularly. We treat a wide range of athletes and dancers, including runners, football players and ballet performers of every age.</p>
    <span class="btn">View More</span>
  </article>
  <article class="card">
    <span class="placeholder" role="img" aria-label="Photo of a friendly podiatry team member in uniform" style="background:linear-gradient(135deg,#dfeaf1,#9fbccf)"></span>
    <h3>All Our Services</h3>
    <p>From time to time, even the best of us can find our feet troubled. When pain limits your ability to walk, stand or work, our caring team is here to help with the right type of treatment and care.</p>
    <span class="btn">View More</span>
  </article>
</div>

<section class="features">
  <span class="features-photo placeholder abs" role="img" aria-label="Photo of a podiatrist in teal scrubs with a smiling patient" style="background:linear-gradient(135deg,#d9eeea,#7fc3b8 60%,#c9b39e)"></span>
  <h2 class="abs">Our Features</h2>
  <div class="feature-bar abs" style="top:1420px">Let Our Kelvale Podiatrists Relieve Your Foot and Ankle Pain</div>
  <p class="feature-copy abs">Whether you are an elite athlete, someone in professional dress, a busy parent, or simply having trouble with daily walking, our experienced podiatrists will find the cause of your pain and plan gentle, effective care suited to your lifestyle and your goals.<br><br>
    <span class="btn">
      <svg width="12" height="12" viewBox="0 0 12 12"><path d="M4 2l4 4-4 4" stroke="#fff" stroke-width="2" fill="none"/></svg>
      Continue Reading
    </span>
  </p>
  <div class="feature-bar abs" style="top:1680px">A Proven Track Record of Correcting Foot Pain in Local Patients</div>
</section>

<h2 class="section-title team-title abs">Meet Our Team</h2>
<div class="team-arrows abs">
  <span class="is-light"><svg width="12" height="12" viewBox="0 0 12 12"><path d="M8 2L4 6l4 4" stroke="#1c9bd3" stroke-width="2" fill="none"/></svg></span>
  <span><svg width="12" height="12" viewBox="0 0 12 12"><path d="M4 2l4 4-4 4" stroke="#fff" stroke-width="2" fill="none"/></svg></span>
</div>
<div class="team-row abs">
  <span class="member-edge"></span>
  <div class="member placeholder" role="img" aria-label="Portrait of a podiatrist" style="background:linear-gradient(180deg,#e5e8ea,#b7c1c8)"></div>
  <div class="member placeholder" role="img" aria-label="Portrait of a foot surgeon" style="background:linear-gradient(180deg,#e5e8ea,#a9b6c1)"></div>
  <div class="member placeholder is-active" role="img" aria-label="Portrait of a podiatrist" style="background:linear-gradient(180deg,#ece8e4,#b9aaa0)">
    <div class="member-caption"><strong>Dr Mara Quill</strong>Podiatrist &nbsp;·&nbsp; Read more</div>
  </div>
  <div class="member placeholder" role="img" aria-label="Portrait of a podiatrist" style="background:linear-gradient(180deg,#e5e8ea,#b4bcc2)"></div>
  <div class="member placeholder" role="img" aria-label="Portrait of a clinic staff member" style="background:linear-gradient(180deg,#e5e8ea,#aab5bd)"></div>
</div>

<section class="band abs">
  <h2 class="band-title abs" style="left:100px;top:30px">Case Histories</h2>
  <h2 class="band-title abs" style="left:660px;top:30px">Free Book</h2>

  <article class="case abs" style="top:100px">
    <span class="placeholder" role="img" aria-label="Photo of a patient with a podiatrist" style="background:linear-gradient(135deg,#f1e4da,#c8a891)"></span>
    <div class="case-body">
      <h3>Plantar fasciitis Case</h3>
      <div class="tag">Health Care</div>
      <p>Persistent heel pain eased after six weeks of tailored care and simple daily stretches at home.</p>
      <div class="icons"><span class="square"></span><span class="square"></span><span class="square"></span></div>
    </div>
  </article>
  <article class="case abs" style="top:330px">
    <span class="placeholder" role="img" aria-label="Photo of a clinician talking with a patient" style="background:linear-gradient(135deg,#e6eef3,#9fb6c6)"></span>
    <div class="case-body">
      <h3>Bunion Case</h3>
      <div class="tag">Health Care</div>
      <p>A painful bunion was corrected with day surgery, letting the patient walk freely within weeks.</p>
      <div class="icons"><span class="square"></span><span class="square"></span><span class="square"></span></div>
    </div>
  </article>
</section>

<div class="book-title abs">Free Foot Surgery Book by Podiatric Surgeon, Dr Nora Bell</div>
<div class="book-cover abs">
  <div class="cover-head">Podiatric Surgery<small>A clear guide to foot and ankle surgery</small></div>
  <span class="placeholder" role="img" aria-label="Photo of a surgical team in theatre" style="background:linear-gradient(135deg,#7fb1cf,#2f6d92)"></span>
</div>
<p class="book-copy abs">This book goes through the most common foot and ankle conditions that can be surgically corrected by our Podiatric Surgeon, Dr Nora Bell.</p>
<span class="btn book-btn abs" style="background:var(--blue-deep)">
  <svg width="12" height="12" viewBox="0 0 12 12"><path d="M4 2l4 4-4 4" stroke="#fff" stroke-width="2" fill="none"/></svg>
  View Details
</span>

<h2 class="section-title contact-title abs">Contact Us</h2>
<p class="contact-sub abs">Please fill out this quick contact form and someone will be in touch with you shortly!</p>

<div class="contact-info abs">
  <h4>Ashvale Office</h4>
  <p><svg width="14" height="14" viewBox="0 0 24 24"><path fill="#1c9bd3" d="M12 2a7 7 0 00-7 7c0 5 7 13 7 13s7-8 7-13a7 7 0 00-7-7zm0 9.5A2.5 2.5 0 1112 6a2.5 2.5 0 010 5.5z"/></svg>42 Harbour Lane,<br>Ashvale, WA 6999</p>
  <h4>Phone</h4>
  <p><svg width="14" height="14" viewBox="0 0 24 24"><path fill="#1c9bd3" d="M6.6 10.8a15 15 0 006.6 6.6l2.2-2.2c.3-.3.7-.4 1-.2 1.1.4 2.3.6 3.6.6.6 0 1 .4 1 1V20c0 .6-.4 1-1 1A17 17 0 013 4c0-.6.4-1 1-1h3.5c.6 0 1 .4 1 1 0 1.3.2 2.5.6 3.6.1.3 0 .7-.2 1z"/></svg>(08) 5550 1820</p>
  <h4>Email</h4>
  <p><svg width="14" height="14" viewBox="0 0 24 24"><path fill="#1c9bd3" d="M3 5h18v14H3zm2 2v.5l7 4.5 7-4.5V7z"/></svg>info@kelvaleheelcare.com.au</p>
</div>

<div class="map placeholder abs" role="img" aria-label="Street map showing the clinic location" style="background:linear-gradient(135deg,#eef0ec,#d9ddd6)"></div>

<form class="form abs">
  <div class="field">Name*</div>
  <div class="field">Phone*</div>
  <div class="field">Email*</div>
  <div class="field is-area">Tell us more</div>
  <span class="btn">Submit</span>
</form>

<nav class="footer-nav abs">
  <span>Home</span><span>Common Problems</span><span>Services</span><span>About Us</span><span>Case Histories</span><span>Helpful Information</span><span>Blog</span><span>Contact</span>
</nav>
<footer class="footer-bottom abs">
  <p class="copyright abs">© 2017 Kelvale Heel Care. All Rights Reserved. Reproduced with Permission. Privacy Policy</p>
  <div class="footer-social abs"><span class="square"></span><span class="square"></span><span class="square"></span><span class="square"></span><span class="square"></span></div>
</footer>

</body>
</html>
```